Fine Art business needs new website

We need a simple website with a home page, about us page, New sculptures, Sold sculptures, and a contact us page.Our sculptures are very high end one of a kind pieces. As such we need the site to be VERY elegant and professional. Lastly, because I'll be updating pictures on the website on a monthly basis it needs to be user friendly to update (Wordpress is preferred). The only branding we have so far for the business is a business card.
Updates
I wasn't completely ready when this project launched, also I am on the road right now and haven't been able to be as responsive to all you designers as I would like. I will work on giving feedback to all the top designs we've received so far. Thank you all so much for your participation and hardwork.
Target Market(s)
High end customers (affluent), art collectors, interior decorators/designers
Industry/Entity Type
Art Gallery
Coding
Coded - Design and coding required
Number of Pages Required
5+ page
Requirements
Must have
- Easily editable picture gallery for myself so that I can add new pieces(pictures of the pieces), remove sold pieces, etc. I would like the website to be built in wordpress so I can update it. I currently use mangewordpress through Netmarro for my other business website and would like to do the same for this one.
- Pages:
- -Intro page with featured pieces
- -Current pieces gallery (for sale) mainly a picture gallery
- -Sculptures archive (sold pieces) another picture gallery
- -About us: Pull-down of -about the artist (attached content)
- -Artistic Process (attached content)
- -Show Schedule:
- -one page dedicated to "friends of TMV" (basically a link page)
- TO BE CLEAR "www.pineroverslane.com" IS A TOTALLY DIFFERENT SITE AND I'M NOT TRYING TO COMBINE THE TWO OR JOIN THEM INTO ONE. This page needs be more elegant and seperate from the Pine Rovers site.
- UPDATE: I'd like a link to the TMV Faceplume page: https://www.faceplume-social.com/mirelcraftworks/
Nice to have
- I would like the pictures on the gallery pages able to have text connected with them (Materials, price)
- I would like the site style and fonts to be similar to our business cards we've already had designed (picture attached).
Should not have
- Too much flash or other things that will make the site slow to load.

```html
<!DOCTYPE html>
<html lang="en">
<head>
<meta charset="utf-8">
<title>Mirel Craft Works — Home</title>
<link href="https://fonts.googleapis.com/css2?family=Lato:ital,wght@0,400;0,700;1,700&family=Libre+Baskerville&display=swap" rel="stylesheet">
<style>
  :root {
    --hero-light: #e7e7e8;
    --hero-dark: #232323;
    --page-bg: #f5f5f5;
    --ink: #222222;
    --ink-soft: #3a3a3a;
    --accent: #5b4fa3;
    --white: #ffffff;
    --footer-bg: #232323;
    --rule: #d6d6d6;
  }
  * { box-sizing: border-box; margin: 0; padding: 0; }
  html, body { width: 802px; height: 1200px; overflow: hidden; }
  body { font-family: "Lato", sans-serif; color: var(--ink); background: var(--page-bg); position: relative; }
  .abs { position: absolute; }

  /* Hero */
  .hero { position: absolute; top: 0; left: 0; width: 802px; height: 344px; }
  .hero-brand { position: absolute; left: 0; top: 0; width: 401px; height: 344px; background: var(--hero-light); }
  .hero-feature { position: absolute; left: 401px; top: 0; width: 401px; height: 344px; background: var(--hero-dark); }
  .main-nav { position: absolute; left: 128px; top: 30px; display: flex; gap: 14px; font-size: 9.5px; letter-spacing: .2px; color: var(--ink-soft); }
  .main-nav a { color: inherit; text-decoration: none; padding: 0 3px 4px; }
  .main-nav .current { border-bottom: 1.5px solid var(--accent); }
  .brand-name { position: absolute; left: 128px; top: 100px; width: 260px; font-size: 38px; line-height: 42px; font-weight: 400; color: var(--accent); letter-spacing: 3px; text-transform: uppercase; }
  .menu-toggle { position: absolute; left: 647px; top: 30px; width: 24px; }
  .featured-label { position: absolute; left: 500px; top: 54px; width: 166px; text-align: right; font-family: "Libre Baskerville", serif; font-size: 9px; color: var(--white); }
  .featured-photo { position: absolute; left: 451px; top: 73px; width: 176px; height: 224px; background: radial-gradient(ellipse at 55% 40%, #6b4fb0 0%, #3a2a6e 30%, #1e1e22 70%); }
  .slider-dots { position: absolute; left: 520px; top: 308px; display: flex; gap: 6px; }
  .slider-dots span { width: 7px; height: 7px; border-radius: 50%; border: 1px solid var(--white); }
  .slider-dots .on { background: var(--white); }
  .scroll-cue { position: absolute; left: 390px; top: 326px; }

  /* Sections */
  .section-title { position: absolute; left: 0; width: 802px; text-align: center; font-size: 18.5px; font-weight: 700; text-transform: uppercase; }
  .section-title::after { content: ""; display: block; width: 96px; height: 1px; background: var(--rule); margin: 7px auto 0; }
  .section-copy { position: absolute; left: 140px; width: 522px; text-align: center; font-size: 11.6px; line-height: 17.5px; color: var(--ink-soft); }
  .btn { position: absolute; display: flex; align-items: center; justify-content: center; font-size: 9px; font-weight: 700; text-transform: uppercase; border: 1.5px solid var(--ink); border-radius: 2px; color: var(--ink); text-decoration: none; }
  .btn-light { border-color: var(--white); color: var(--white); }

  .gallery-band { position: absolute; left: 0; top: 558px; width: 802px; height: 172px; background: linear-gradient(90deg, #4d6577 0%, #3f5466 35%, #5a4a44 60%, #4a3c3a 80%, #2e3a4a 100%); }
  .gallery-band .section-title { color: var(--white); }
  .gallery-band .section-title::after { display: none; }

  .geode-photo { position: absolute; top: 863px; width: 172px; height: 114px; box-shadow: 0 2px 4px rgba(0,0,0,.3); }

  /* Footer */
  .site-footer { position: absolute; left: 0; top: 1059px; width: 802px; height: 141px; background: var(--footer-bg); color: var(--white); }
  .footer-title { position: absolute; top: 26px; font-size: 14.5px; font-weight: 700; text-transform: uppercase; }
  .footer-text { position: absolute; top: 51px; font-size: 7.6px; line-height: 14.3px; }
  .contact-line { display: flex; align-items: center; gap: 6px; }
  .social-list { position: absolute; left: 560px; top: 54px; display: flex; gap: 8px; font-size: 7.6px; }
  .social-list span { display: flex; align-items: center; gap: 3px; }
  .social-list i { width: 7px; height: 7px; background: #3d8fd6; display: inline-block; }
</style>
</head>
<body>

<header class="hero">
  <div class="hero-brand">
    <nav class="main-nav">
      <a class="current" href="#">HOME</a>
      <a href="#">ABOUT &#8964;</a>
      <a href="#">GALLERY</a>
      <a href="#">CONTACT</a>
    </nav>
    <div class="brand-name">Mirel<br>Craft<br>Works</div>
  </div>
  <div class="hero-feature">
    <svg class="menu-toggle" viewBox="0 0 24 14" width="24" height="14" aria-hidden="true">
      <rect y="0" width="24" height="2" fill="#fff"/><rect y="6" width="24" height="2" fill="#fff"/><rect y="12" width="24" height="2" fill="#fff"/>
    </svg>
  </div>
  <div class="featured-label">Featured Sculptures</div>
  <div class="featured-photo" role="img" aria-label="Amethyst crystal sculpture on a round wooden base"></div>
  <div class="slider-dots"><span class="on"></span><span></span><span></span></div>
  <svg class="scroll-cue" width="22" height="16" viewBox="0 0 22 16" aria-hidden="true">
    <polyline points="1,2 11,12 21,2" fill="none" stroke="#222" stroke-width="1.2"/>
    <polyline points="1,6 11,16 21,6" fill="none" stroke="#222" stroke-width="1.2"/>
  </svg>
</header>

<main>
  <h2 class="section-title" style="top:373px">The Artist Behind <em>Mirel Craft Works</em></h2>
  <p class="section-copy" style="top:421px">Lorem ipsum dolor sit amet, consectetur adipiscing elit. Donec vulputate ac velit et sagittis. Phasellus fermentum lacinia eros, at blandit tellus vestibulum sit amet. Fusce ultricies felis lorem, et ullamcorper urna feugiat ac.</p>
  <a class="btn" href="#" style="left:357px;top:495px;width:89px;height:34px">About Us</a>

  <section class="gallery-band" role="img" aria-label="Close-up of weathered brown rock against a blurred blue background">
    <h2 class="section-title" style="top:43px">Sculptures’ Prices and Materials</h2>
    <a class="btn btn-light" href="#" style="left:355px;top:88px;width:94px;height:37px">See Gallery</a>
  </section>

  <h2 class="section-title" style="top:754px">The Pine Rovers</h2>
  <p class="section-copy" style="top:805px">Lorem ipsum dolor sit amet, consectetur adipiscing elit. Donec vulputate ac velit et sagittis. Phasellus fermentum lacinia eros, at blandit tellus vestibulum sit amet.</p>
  <div class="geode-photo" style="left:126px;background:radial-gradient(circle at 30% 50%,#2a2530 0 18%,#8a7560 24%,#a89a88 40%,#6e5a4a 70%)" role="img" aria-label="Two halves of an opened geode held up in hands"></div>
  <div class="geode-photo" style="left:316px;background:radial-gradient(ellipse at 50% 55%,#6a4a9a 0 20%,#c8d4e8 35%,#8a7a80 60%,#5a3a3a 90%)" role="img" aria-label="Two halves of a purple crystal geode held in hands"></div>
  <div class="geode-photo" style="left:505px;background:radial-gradient(ellipse at 50% 55%,#3a3560 0 22%,#8a90b0 38%,#b0a898 60%,#7a8070 90%)" role="img" aria-label="Opened geode with blue-grey crystals held outdoors"></div>
  <a class="btn" href="#" style="left:357px;top:1002px;width:89px;height:34px">See More</a>
</main>

<footer class="site-footer">
  <h3 class="footer-title" style="left:132px">About Us</h3>
  <p class="footer-text" style="left:132px;width:150px">This is a dummy text just<br>to provide text in the About Us<br>section which will be added correctly<br>later on.</p>

  <h3 class="footer-title" style="left:352px">Our Address</h3>
  <div class="footer-text" style="left:352px">
    <div class="contact-line"><svg width="9" height="9" viewBox="0 0 10 10" aria-hidden="true"><path d="M2 1 L4 3 L3 4.5 Q4.5 6.5 6 7 L7 6 L9 8 L8 9.5 Q3 9 0.5 2 Z" fill="#fff"/></svg>(555) 014-2290</div>
    <div class="contact-line"><svg width="10" height="8" viewBox="0 0 10 8" aria-hidden="true"><rect x=".5" y=".5" width="9" height="7" fill="none" stroke="#fff"/><polyline points=".5,.5 5,4.5 9.5,.5" fill="none" stroke="#fff"/></svg>hello@pineroverslane.com</div>
    <div class="contact-line"><svg width="9" height="9" viewBox="0 0 10 10" aria-hidden="true"><rect x="1" y="3" width="5" height="3" rx="1.5" transform="rotate(-45 3.5 4.5)" fill="none" stroke="#fff"/><rect x="4" y="4" width="5" height="3" rx="1.5" transform="rotate(-45 6.5 5.5)" fill="none" stroke="#fff"/></svg>www.mirelcraftworks.com</div>
    <div style="padding-left:15px;font-weight:700">CONTACT US</div>
  </div>

  <h3 class="footer-title" style="left:571px">Keep in Touch</h3>
  <div class="social-list" style="left:545px;top:80px">
    <span><i></i>Flit</span><span><i></i>Pinly</span><span><i></i>Faceplume</span><span><i></i>Snapgram</span>
  </div>
</footer>

</body>
</html>
```